Super elegant, crisp & clean Business card design required

We recently upgraded our branding - which is on our website - talvendoraphoto.com

I would like a simple, yet elegant, clean business card design please.

The font of my logo is Cinzel - and because of the natural colour - it's best to have this on a black background.

I would like to have the back of the business card - with simply my logo.

PLEASE DO NOT SUBMIT A COMPLICATED / UNCLEAN DESIGN

Industry/Entity Type

Business

Contact Information for Business Card

Talven Doroshko Photography

Font styles to use
Other font styles liked:
• Cinzel

Requirements
Must have
• A backpage with nothing but my logo
• Simple design - stands out
Should not have
• Colour that dont align with my logo
• Over complicated '/ non symmetrical design

```html
<!DOCTYPE html>
<html lang="en">
<head>
<meta charset="utf-8">
<title>Talven Doroshko Photography – Business Card</title>
<link rel="stylesheet" href="https://fonts.googleapis.com/css2?family=Cinzel:wght@400;700&display=swap">
<style>
  :root {
    --backdrop: #2b2b2b;
    --card-light: #f7f7f7;
    --card-light-edge: #e6e6e6;
    --card-dark: #141517;
    --gold-taupe: #7b6a55;
    --gold-taupe-soft: #6f604e;
    --text-grey: #8c8478;
  }
  * { margin: 0; padding: 0; box-sizing: border-box; }
  html, body {
    width: 1200px; height: 965px; overflow: hidden;
    background: var(--backdrop);
  }
  .canvas { position: relative; width: 1200px; height: 965px; }
  .card {
    position: absolute; left: 246px; width: 710px; height: 402px;
    display: flex; flex-direction: column; align-items: center;
    font-family: "Cinzel", serif;
  }
  .card--front {
    top: 60px;
    background: radial-gradient(ellipse at 50% 40%, #ffffff 0%, var(--card-light) 55%, var(--card-light-edge) 100%);
    box-shadow: 0 2px 4px rgba(0,0,0,.5);
  }
  .card--back {
    top: 505px;
    background: var(--card-dark);
    justify-content: center;
  }
  .brand { display: flex; flex-direction: column; align-items: center; }
  .brand__circle {
    width: 80px; height: 80px; border-radius: 50%;
    border: 1.5px solid var(--gold-taupe);
  }
  .brand__name {
    margin-top: 22px; font-weight: 400; font-size: 20px;
    letter-spacing: 1px; color: var(--gold-taupe); white-space: nowrap;
  }
  .card--front .brand { margin-top: 40px; }
  .card--back .brand__circle { border-color: var(--gold-taupe-soft); }
  .card--back .brand__name { color: var(--gold-taupe-soft); }
  .person { margin-top: 46px; text-align: center; }
  .person__name { font-weight: 700; font-size: 22px; color: var(--gold-taupe); line-height: 1; }
  .person__title { font-size: 16px; color: var(--text-grey); margin-top: 6px; }
  .contact { margin-top: 42px; text-align: center; font-size: 15px; color: var(--text-grey); line-height: 21px; }
  .contact__row { display: flex; justify-content: center; align-items: center; gap: 6px; }
  .contact__item { display: inline-flex; align-items: center; gap: 6px; }
  .contact__item + .contact__item { margin-left: 8px; }
  .contact__phone { font-size: 16px; }
  .icon { width: 14px; height: 14px; fill: var(--gold-taupe-soft); }
</style>
</head>
<body>
<div class="canvas">
  <section class="card card--front">
    <div class="brand">
      <div class="brand__circle"></div>
      <div class="brand__name">Talven Doroshko Photography</div>
    </div>
    <div class="person">
      <div class="person__name">Talven Doroshko</div>
      <div class="person__title">Photographer</div>
    </div>
    <div class="contact">
      <div class="contact__row">
        <span class="contact__item contact__phone">
          <svg class="icon" viewBox="0 0 16 16"><path d="M3.6 1.2l2.3 2.6-1.3 1.9c.9 2.1 2.5 3.8 4.6 4.8l1.9-1.3 2.6 2.3-1.3 2.3C7.4 13.6 2.4 8.6 1.3 2.5z"/></svg>
          07 555 210 384
        </span>
        <span class="contact__item">
          <svg class="icon" viewBox="0 0 16 16"><path d="M1 3.5h14v9H1z M1.6 4.1L8 9l6.4-4.9" fill="none" stroke="#6f604e" stroke-width="0"/><path d="M1 3.5h14L8 8.5z"/><path d="M1 4.8l4.6 3.5L1 12.5z M15 4.8l-4.6 3.5L15 12.5z M6.4 9L8 10.2 9.6 9l4.6 3.5H1.8z"/></svg>
          info@talvendoraphoto.com
        </span>
      </div>
      <div class="contact__row">
        <span class="contact__item">
          <svg class="icon" viewBox="0 0 16 16"><g fill="none" stroke="#6f604e" stroke-width="1.2"><circle cx="8" cy="8" r="6.5"/><ellipse cx="8" cy="8" rx="3" ry="6.5"/><path d="M1.5 8h13M2.5 4.8h11M2.5 11.2h11"/></g></svg>
          www.talvendoraphoto.com
        </span>
      </div>
    </div>
  </section>

  <section class="card card--back">
    <div class="brand">
      <div class="brand__circle"></div>
      <div class="brand__name">Talven Doroshko Photography</div>
    </div>
  </section>
</div>
</body>
</html>
```